Combat Sports news website design

Redesigning our existing website to make it more modern, responsive and suitable for our needs. The design needs to take in to account all aspects of our current website structure and services. View the existing website at https://www.ringpulse.co.nz

Particular attention should be paid to our livestream service, which is growing and needs to be much more user friendly to the current experience.

The homepage, article listings and article pages need designs.

Target Market(s)

Combat sports fans

Industry/Entity Type

Media

Coding

Coded - Design and coding required

Number of Pages Required

5+ page

Font styles to use
Sans Serif

Requirements
Must have
• All the functionality of the existing website must be taken in to account, and improved upon.
New design must incorporate our existing logo/colour scheme as this has only just been designed.

```html
<!DOCTYPE html>
<html lang="en">
<head>
<meta charset="utf-8">
<title>Ring Pulse — Combat Sports News</title>
<link href="https://fonts.googleapis.com/css2?family=Montserrat:wght@400;500;600;700;800&family=Oswald:wght@500;600;700&display=swap" rel="stylesheet">
<style>
:root{
  --navy:#1b2232;
  --red:#c4161c;
  --ink:#111;
  --grey-box:#f3f3f3;
  --ad:#cfcfcf;
  --footer:#2b2b2b;
  --footer-muted:#5c5c5c;
}
*{box-sizing:border-box;margin:0;padding:0}
html,body{width:1200px;height:3657px;overflow:hidden;background:#fff}
body{position:relative;font-family:"Montserrat",sans-serif;color:var(--ink)}
.abs{position:absolute}
a{color:inherit;text-decoration:none}

/* header */
.site-header{position:absolute;left:0;top:0;width:1200px;height:110px;background:var(--navy)}
.main-nav{position:absolute;top:0;left:0;width:1200px;height:58px;font-family:"Oswald",sans-serif;font-weight:600;color:#fff;font-size:14px;text-transform:uppercase}
.main-nav a{position:absolute;top:20px}
.main-nav .active{font-size:17px;top:17px}
.main-nav .active::after{content:"";position:absolute;left:-20px;right:-20px;top:39px;height:3px;background:var(--red)}
.main-nav .brand{top:12px;left:566px;font-weight:700;font-size:19px;line-height:17px;text-align:center;width:70px}
.sub-nav{position:absolute;top:74px;left:136px;font-family:"Oswald",sans-serif;font-weight:600;font-size:13px;color:#8a8f9b;display:flex;gap:30px;text-transform:uppercase}
.sub-nav .on{color:#fff}

/* hero */
.hero{position:absolute;left:0;top:110px;width:1200px;height:512px;background:linear-gradient(135deg,#3a3f48 0%,#23272f 45%,#4a4f55 100%)}
.hero-copy{position:absolute;left:210px;top:92px;color:#fff}
.hero-copy h1{font-weight:800;font-size:43px;line-height:50px;letter-spacing:.5px;width:760px}
.read-more{display:inline-flex;align-items:center;gap:6px;font-weight:500;letter-spacing:1px;text-transform:uppercase;color:#fff}
.hero-copy .read-more{font-size:17px;margin-top:12px}
.feature{position:absolute;top:467px;height:330px;color:#fff}
.feature h2{position:absolute;font-weight:800;font-size:20px;line-height:25px;letter-spacing:.8px}
.feature .read-more{position:absolute;font-size:13px}

/* section headings */
.section-title{position:absolute;font-weight:700;font-size:20px;letter-spacing:1px;text-transform:uppercase;padding-left:14px;line-height:24px}
.section-title::before{content:"";position:absolute;left:0;top:0;width:7px;height:24px;background:var(--red)}

/* icons */
.ic-clock,.ic-user{display:inline-block;width:11px;height:11px;border:1.2px solid #333;border-radius:50%;position:relative;flex:none}
.ic-clock::after{content:"";position:absolute;left:4px;top:1.5px;width:2.5px;height:3.5px;border-left:1.2px solid #333;border-bottom:1.2px solid #333}
.ic-user::after{content:"";position:absolute;left:3px;top:1.5px;width:3px;height:3px;border:1.2px solid #333;border-radius:50%}

/* event */
.thumb{background:linear-gradient(135deg,#3a4150,#1f2530)}
.event h3{font-weight:700;font-size:16px}
.meta-row{display:flex;align-items:center;gap:8px;font-size:10px;color:#333;margin-top:14px}
.btn{display:inline-flex;align-items:center;gap:5px;background:var(--red);color:#fff;font-size:9px;font-weight:600;letter-spacing:1px;text-transform:uppercase;padding:0 16px;height:31px}

/* cards */
.news-card{position:absolute;width:300px}
.news-card .thumb{width:298px;height:179px}
.news-card h3{font-weight:700;font-size:16px;line-height:20px;margin:20px 6px 0}
.news-card p{font-size:11.5px;line-height:14px;color:#333;margin:14px 6px 0}
.meta{list-style:none;margin:14px 6px 0;font-size:8px;letter-spacing:.6px;color:#333;text-transform:uppercase}
.meta li{display:flex;align-items:center;gap:8px;height:20px;font-size:8px;color:#333}
.news-card .btn{margin:14px 6px 0}
.mini{position:absolute;left:433px;width:340px;height:114px}
.mini .thumb{position:absolute;left:0;top:0;width:135px;height:114px}
.mini h4{position:absolute;left:154px;top:16px;width:190px;font-size:12.5px;font-weight:600;line-height:17px}
.mini .meta{position:absolute;left:154px;top:52px;margin:0}
.mini .more{position:absolute;left:154px;top:84px;color:var(--red);font-size:10px;letter-spacing:1px;font-weight:500;display:flex;gap:5px;align-items:center}

/* sidebar */
.side-box{position:absolute;left:801px;width:298px;background:var(--grey-box)}
.side-box .section-title{font-size:15px;left:21px;top:24px;padding-left:16px;line-height:20px}
.side-box .section-title::before{height:20px;width:6px}
.headline-list{position:absolute;left:20px;top:72px;width:260px;list-style:none}
.headline-list > li{color:var(--red);font-size:13px;line-height:16px}
.headline-list .meta{margin:6px 0 0}
.ad-slot{position:absolute;left:22px;top:62px;width:253px;height:162px;background:var(--ad)}
.follow{position:absolute;height:32px;width:119px;display:flex;align-items:center;justify-content:center;gap:7px;color:#fff;font-size:11px;font-weight:700;letter-spacing:1px}
.follow i{width:12px;height:12px;border-radius:50%;background:#fff;display:block}
.poll-q{position:absolute;left:25px;top:74px;font-size:12px;font-weight:700;letter-spacing:1px;line-height:15px;width:240px}
.poll-opt{position:absolute;left:24px;display:flex;align-items:center;gap:18px;font-size:12px;font-weight:700;letter-spacing:1px}
.radio{width:26px;height:26px;border-radius:50%;border:2px solid var(--red);display:flex;align-items:center;justify-content:center}
.radio.on::after{content:"";width:16px;height:16px;border-radius:50%;background:var(--red)}
.poll-btn{position:absolute;top:357px;height:31px;background:var(--red);color:#fff;font-size:11px;letter-spacing:1px;display:flex;align-items:center;justify-content:center}

/* footer */
.site-footer{position:absolute;left:0;top:3248px;width:1200px;height:409px;background:var(--footer);color:#fff}
.footer-brand{position:absolute;left:82px;top:24px;font-weight:800;font-size:46px;line-height:48px;color:#fff;width:170px}
.bio h5{font-size:18px;font-weight:700;color:#b7b7b7}
.bio p{font-size:13.5px;line-height:16px;color:#8a8a8a;text-align:justify;margin-top:4px}
.f-head{position:absolute;font-size:12px;color:var(--footer-muted);letter-spacing:.5px;text-transform:uppercase}
.f-list{position:absolute;list-style:none;font-size:14px;line-height:22px;color:#ddd}
.f-input{position:absolute;left:858px;width:180px;height:23px;background:#4a4a4a;font-size:9px;color:#ccc;padding:6px 9px}
.social-dot{position:absolute;top:312px;width:18px;height:18px;border-radius:50%;background:#bdbdbd}
</style>
</head>
<body>

<header class="site-header">
  <nav class="main-nav">
    <a style="left:136px">Home</a>
    <a class="active" style="left:244px">Categories</a>
    <a style="left:390px">Live Events</a>
    <a class="brand" href="https://www.ringpulse.co.nz">Ring<br>Pulse</a>
    <a style="left:744px">Contact Us</a>
    <a style="left:852px">About Us</a>
    <a style="left:960px">Login &nbsp;/&nbsp; Register</a>
    <svg class="abs" style="left:1096px;top:18px" width="20" height="20" viewBox="0 0 20 20" fill="none" stroke="#fff" stroke-width="2"><circle cx="8" cy="8" r="6"/><path d="M13 13l5 5"/></svg>
  </nav>
  <nav class="sub-nav">
    <a>MMA</a><a class="on">Kickboxing</a><a>Boxing</a><a>Wrestling</a><a>ZFW</a><a>NEXFC</a>
  </nav>
</header>

<section class="hero" role="img" aria-label="Kickboxers exchanging blows in the ring">
  <div class="hero-copy">
    <h1>TANE WHITLOCK STEPS INTO SUMMIT 80KG DIVISION ON SHORT NOTICE</h1>
    <a class="read-more">Read more <svg width="16" height="12" viewBox="0 0 16 12" fill="none" stroke="#fff" stroke-width="2"><path d="M1 6h13M9 1l5 5-5 5"/></svg></a>
  </div>
</section>

<article class="feature thumb" style="left:100px;width:316px;background:linear-gradient(160deg,#4a4e55,#1d2027)" role="img" aria-label="Fighter in the ring after a bout">
  <h2 style="left:48px;top:124px;width:240px">TANE WHITLOCK STEPS INTO SUMMIT 80KG DIVISION ON SHORT NOTICE</h2>
  <a class="read-more" style="left:48px;top:232px">Read more <svg width="14" height="10" viewBox="0 0 16 12" fill="none" stroke="#fff" stroke-width="2"><path d="M1 6h13M9 1l5 5-5 5"/></svg></a>
</article>
<article class="feature thumb" style="left:433px;width:666px;background:linear-gradient(135deg,#2a2f4a,#1a1d2c 60%,#3b3f5c)" role="img" aria-label="Fight team posing with a champion belt">
  <h2 style="left:47px;top:124px;width:470px">TANE WHITLOCK STEPS INTO SUMMIT 80KG DIVISION ON SHORT NOTICE</h2>
  <a class="read-more" style="left:47px;top:187px">Read more <svg width="14" height="10" viewBox="0 0 16 12" fill="none" stroke="#fff" stroke-width="2"><path d="M1 6h13M9 1l5 5-5 5"/></svg></a>
</article>

<h2 class="section-title" style="left:100px;top:877px">Upcoming Events</h2>
<div class="thumb abs" style="left:100px;top:949px;width:333px;height:211px;background:linear-gradient(135deg,#2b3548,#141a25)" role="img" aria-label="Muay Thai Strike Series event poster"></div>
<div class="event abs" style="left:458px;top:972px">
  <h3>Summit - Muay Thai Strike Series</h3>
  <div class="meta-row" style="margin-top:20px"><svg width="14" height="16" viewBox="0 0 14 16" fill="none" stroke="#333" stroke-width="1.3"><path d="M7 15s5-5 5-9A5 5 0 0 0 2 6c0 4 5 9 5 9z"/><circle cx="7" cy="6" r="2"/></svg>Harbour Strike Gym, Northcote Auckland</div>
  <div class="meta-row"><svg width="14" height="14" viewBox="0 0 14 14" fill="none" stroke="#333" stroke-width="1.3"><circle cx="7" cy="7" r="6"/><path d="M7 3.5V7l2.5 1.5"/></svg>17:00PM &nbsp;01 MAY 2021</div>
  <div class="meta-row"><svg width="14" height="14" viewBox="0 0 14 14" fill="none" stroke="#333" stroke-width="1.3"><path d="M1 7l6-6h6v6l-6 6z"/><circle cx="10" cy="4" r="1"/></svg>$20.00</div>
  <a class="btn" style="margin-top:18px">Learn more &#8594;</a>
</div>

<h2 class="section-title" style="left:100px;top:1245px">Recent Headlines</h2>
<article class="news-card" style="left:102px;top:1311px">
  <div class="thumb" role="img" aria-label="Fighters celebrating with championship belts" style="background:linear-gradient(160deg,#2c3c8a,#2a2430)"></div>
  <h3>Vantel predicts hard fight at Summit this Saturday</h3>
  <p>Corey Vantel is a 20-year-old Muay Thai phenom fighting out of New Plymouth, Taranaki....</p>
  <ul class="meta"><li><i class="ic-clock"></i>12:00PM &nbsp;WED 28 APR</li><li><i class="ic-user"></i>Carla Jennings</li></ul>
  <a class="btn">Read more &#8594;</a>
</article>
<div class="mini" style="top:1311px"><div class="thumb" role="img" aria-label="Kickboxers exchanging strikes" style="background:linear-gradient(135deg,#555,#1e1e1e)"></div><h4>Vantel predicts hard fight at Summit this Saturday</h4><ul class="meta"><li><i class="ic-clock"></i>12:00PM &nbsp;WED 28 APR</li></ul><a class="more">READ MORE &#8594;</a></div>
<div class="mini" style="top:1463px"><div class="thumb" role="img" aria-label="Muay Thai Strike Series poster" style="background:linear-gradient(135deg,#34405a,#141a25)"></div><h4>Vantel predicts hard fight at Summit this Saturday</h4><ul class="meta"><li><i class="ic-clock"></i>12:00PM &nbsp;WED 28 APR</li></ul><a class="more">READ MORE &#8594;</a></div>
<div class="mini" style="top:1620px"><div class="thumb" role="img" aria-label="Boxing fight card poster" style="background:linear-gradient(135deg,#3a3a3a,#7a2025)"></div><h4>Vantel predicts hard fight at Summit this Saturday</h4><ul class="meta"><li><i class="ic-clock"></i>12:00PM &nbsp;WED 28 APR</li></ul><a class="more">READ MORE &#8594;</a></div>

<h2 class="section-title" style="left:98px;top:1803px">Earlier News</h2>
<article class="news-card" style="left:100px;top:1872px"><div class="thumb" role="img" aria-label="Fighters celebrating with championship belts" style="background:linear-gradient(160deg,#2c3c8a,#2a2430)"></div><h3>Vantel predicts hard fight at Summit this Saturday</h3><p>Corey Vantel is a 20-year-old Muay Thai phenom fighting out of New Plymouth, Taranaki....</p><ul class="meta"><li><i class="ic-clock"></i>12:00PM &nbsp;WED 28 APR</li><li><i class="ic-user"></i>Carla Jennings</li></ul><a class="btn">Read more &#8594;</a></article>
<article class="news-card" style="left:437px;top:1872px"><div class="thumb" role="img" aria-label="Fighter in the ring under green lights" style="background:linear-gradient(160deg,#2f7a5a,#1c2a3a)"></div><h3>Vantel predicts hard fight at Summit this Saturday</h3><p>Corey Vantel is a 20-year-old Muay Thai phenom fighting out of New Plymouth, Taranaki....</p><ul class="meta"><li><i class="ic-clock"></i>12:00PM &nbsp;WED 28 APR</li><li><i class="ic-user"></i>Carla Jennings</li></ul><a class="btn">Read more &#8594;</a></article>
<article class="news-card" style="left:100px;top:2328px"><div class="thumb" role="img" aria-label="Referee raising a winner's hand in the ring" style="background:linear-gradient(160deg,#4a4a52,#151518)"></div><h3>Vantel predicts hard fight at Summit this Saturday</h3><p>Corey Vantel is a 20-year-old Muay Thai phenom fighting out of New Plymouth, Taranaki....</p><ul class="meta"><li><i class="ic-clock"></i>12:00PM &nbsp;WED 28 APR</li><li><i class="ic-user"></i>Carla Jennings</li></ul><a class="btn">Read more &#8594;</a></article>
<article class="news-card" style="left:437px;top:2322px"><div class="thumb" role="img" aria-label="Kickboxers fighting in a dark arena" style="background:linear-gradient(160deg,#4d4640,#151313)"></div><h3 style="margin-top:26px">Vantel predicts hard fight at Summit this Saturday</h3><p>Corey Vantel is a 20-year-old Muay Thai phenom fighting out of New Plymouth, Taranaki....</p><ul class="meta"><li><i class="ic-clock"></i>12:00PM &nbsp;WED 28 APR</li><li><i class="ic-user"></i>Carla Jennings</li></ul><a class="btn">Read more &#8594;</a></article>
<article class="news-card" style="left:88px;top:2784px"><div class="thumb" role="img" aria-label="Muay Thai Strike Series poster" style="background:linear-gradient(135deg,#34405a,#141a25)"></div><h3>Vantel predicts hard fight at Summit this Saturday</h3><p>Corey Vantel is a 20-year-old Muay Thai phenom fighting out of New Plymouth, Taranaki....</p><ul class="meta"><li><i class="ic-clock"></i>12:00PM &nbsp;WED 28 APR</li><li><i class="ic-user"></i>Carla Jennings</li></ul><a class="btn">Read more &#8594;</a></article>
<article class="news-card" style="left:425px;top:2784px"><div class="thumb" role="img" aria-label="Fight team posing in a gym with belts" style="background:linear-gradient(135deg,#6a6a70,#1d1d22)"></div><h3>Vantel predicts hard fight at Summit this Saturday</h3><p>Corey Vantel is a 20-year-old Muay Thai phenom fighting out of New Plymouth, Taranaki....</p><ul class="meta"><li><i class="ic-clock"></i>12:00PM &nbsp;WED 28 APR</li><li><i class="ic-user"></i>Carla Jennings</li></ul><a class="btn">Read more &#8594;</a></article>

<aside>
  <section class="side-box" style="top:934px;height:580px">
    <h2 class="section-title">Latest Headlines</h2>
    <ul class="headline-list">
      <li style="height:79px">Mika Rowe looking to avenge her only loss<ul class="meta"><li><i class="ic-clock"></i>12:00PM &nbsp;WED 28 APR</li></ul></li>
      <li style="height:81px">Tane Whitlock steps into Summit 80kg division on short notice<ul class="meta"><li><i class="ic-clock"></i>12:00PM &nbsp;WED 28 APR</li></ul></li>
      <li style="height:95px">Five NZ Kick League Cup winners crowned at Rise Fight 9<ul class="meta" style="margin-top:22px"><li><i class="ic-clock"></i>12:00PM &nbsp;WED 28 APR</li></ul></li>
      <li style="height:86px">Vantel predicts hard fight at Summit this Saturday<ul class="meta"><li><i class="ic-clock"></i>12:00PM &nbsp;WED 28 APR</li></ul></li>
      <li style="height:62px">Prime Fight Series 2 results<ul class="meta"><li><i class="ic-clock"></i>12:00PM &nbsp;WED 28 APR</li></ul></li>
      <li>VIDEO: "I'm bringing pain!" - Dane Corrick declares war on Josh Palmer<ul class="meta"><li><i class="ic-clock"></i>12:00PM &nbsp;WED 28 APR</li></ul></li>
    </ul>
  </section>
  <section class="side-box" style="top:1548px;height:244px">
    <h2 class="section-title">Advertisement</h2><div class="ad-slot"></div>
  </section>
  <section class="side-box" style="top:1823px;height:172px">
    <h2 class="section-title">Follow Us</h2>
    <a class="follow" style="left:24px;top:66px;background:#8a3ab9"><i></i>FOLLOW</a>
    <a class="follow" style="left:157px;top:66px;background:#1da1f2"><i></i>FOLLOW</a>
    <a class="follow" style="left:24px;top:112px;background:#3b5998"><i></i>FOLLOW</a>
  </section>
  <section class="side-box" style="top:2025px;height:243px">
    <h2 class="section-title">Advertisement</h2><div class="ad-slot" style="left:21px"></div>
  </section>
  <section class="side-box" style="top:2299px;height:402px">
    <h2 class="section-title" style="left:20px">Opinion Poll</h2>
    <p class="poll-q">WHAT COMBAT SPORT DO YOU PREFER?</p>
    <label class="poll-opt" style="top:124px"><span class="radio on"></span>MMA</label>
    <label class="poll-opt" style="top:165px"><span class="radio"></span>WRESTLING</label>
    <label class="poll-opt" style="top:206px"><span class="radio"></span>KICKBOXING</label>
    <label class="poll-opt" style="top:246px"><span class="radio"></span>MUAY THAI</label>
    <label class="poll-opt" style="top:287px"><span class="radio"></span>ALL OF THE ABOVE</label>
    <a class="poll-btn" style="left:25px;width:81px">VOTE</a>
    <a class="poll-btn" style="left:117px;width:141px">SHOW RESULTS</a>
  </section>
</aside>

<footer class="site-footer">
  <div class="footer-brand">RING<br>PULSE</div>
  <div class="bio abs" style="left:82px;top:152px;width:245px">
    <h5>Lena Harwood</h5>
    <p>Lena has worked in the media industry since she was 15-years-old. She has worked in both radio and print, and is the co-founder and editor-in-chief of Ring Pulse. As well as being the Ring Pulse Editor, she focuses on writing for muti-discipline combat sports.</p>
  </div>
  <p class="abs" style="left:82px;top:386px;font-size:8px;color:#bbb">Copyright © 2021-2022 RING PULSE All Rights Reserved</p>

  <p class="f-head" style="left:453px;top:38px">Site Map</p>
  <ul class="f-list" style="left:453px;top:58px"><li>Home</li><li>MMA</li><li>Kickboxing</li><li>Boxing</li><li>Wrestling</li><li>ZFW</li><li>NEXFC</li><li>Live events</li></ul>
  <p class="f-head" style="left:613px;top:38px">Usefull Links</p>
  <ul class="f-list" style="left:613px;top:58px"><li>Site Terms</li><li>Advertisement</li><li>Contact us</li><li>Privacy</li></ul>
  <p class="f-head" style="left:453px;top:276px">Get in touch</p>
  <span class="social-dot" style="left:450px"></span>
  <span class="social-dot" style="left:500px"></span>
  <span class="social-dot" style="left:554px"></span>
  <span class="social-dot" style="left:610px"></span>
  <p class="f-head" style="left:453px;top:378px;font-size:13px">Need help?</p>
  <svg class="abs" style="left:546px;top:375px" width="22" height="16" viewBox="0 0 22 16" fill="none" stroke="#bbb" stroke-width="1.5"><rect x="1" y="1" width="20" height="14"/><path d="M1 1l10 8 10-8"/></svg>
  <a class="abs" style="left:576px;top:376px;font-size:13px;color:#bbb">newsdesk@ringpulse.co.nz</a>

  <p class="f-head" style="left:858px;top:38px">Contact us</p>
  <div class="f-input" style="top:60px">First name</div>
  <div class="f-input" style="top:91px">Last name</div>
  <div class="f-input" style="top:121px">Email</div>
  <div class="f-input" style="top:152px">Phone / Mobile</div>
  <div class="f-input" style="top:186px;width:258px;height:150px">Message</div>
  <a class="abs" style="left:858px;top:346px;width:97px;height:26px;background:var(--red);color:#fff;font-size:12px;display:flex;align-items:center;justify-content:center">Submit</a>
</footer>

</body>
</html>
```